Need Business Card for our Real Estate Business with Sales Executive's Picture

PANTONE 484 C ( RED)

PANTONE 2766 C ( BLUE

Industry/Entity Type

Real Estate

Contact Information for Business Card

Name, Mobile, email, & picture of Person
Agency Phone, address, Web address

Requirements
Must have
• Our Logo Colours, Agent Picture,

```html
<!DOCTYPE html>
<html lang="en">
<head>
<meta charset="utf-8">
<title>Corval Real Estate – Business Card</title>
<link rel="stylesheet" href="https://fonts.googleapis.com/css2?family=Roboto:wght@400;500;700&family=Cinzel:wght@500&display=swap">
<style>
  :root {
    --navy: #0b1538;
    --maroon: #620a13;
    --paper: #f1f1f0;
    --white: #ffffff;
    --backdrop: #e4e1dc;
  }
  html, body {
    margin: 0;
    padding: 0;
    overflow: hidden;
  }
  body {
    width: 1200px;
    height: 960px;
    background: var(--backdrop);
    position: relative;
    font-family: "Roboto", Arial, sans-serif;
  }
  .card {
    position: absolute;
    width: 600px;
    height: 343px;
    overflow: hidden;
    box-shadow: 0 2px 6px rgba(0,0,0,0.25);
  }
  .card--front { left: 314px; top: 113px; background: var(--paper); }
  .card--back { left: 311px; top: 472px; background: var(--maroon); }

  .card__shape { position: absolute; left: 0; top: 0; }

  .brand {
    position: absolute;
    display: flex;
    align-items: center;
    gap: 10px;
    font-family: "Cinzel", Georgia, serif;
    font-weight: 500;
    white-space: nowrap;
  }
  .brand__mark { width: 12px; height: 12px; }
  .card--front .brand { left: 62px; top: 178px; font-size: 32px; color: var(--navy); }
  .card--front .brand__mark { background: var(--maroon); }
  .card--back .brand { left: 336px; top: 222px; font-size: 32px; color: var(--white); }
  .card--back .brand__mark { background: var(--white); }

  .contact {
    position: absolute;
    left: 393px;
    top: 62px;
    color: var(--white);
  }
  .contact__name { margin: 0; font-size: 19px; font-weight: 700; letter-spacing: 0.2px; }
  .contact__role { margin: 3px 0 0; font-size: 15px; font-weight: 500; }
  .contact__address { margin: 27px 0 0; font-size: 14px; line-height: 18px; font-style: normal; }
  .contact__list { list-style: none; margin: 10px 0 0; padding: 0; font-size: 14px; line-height: 19.3px; }
  .contact__list li { display: flex; align-items: center; gap: 9px; }
  .contact__icon { width: 14px; height: 14px; flex: none; fill: var(--white); }

  .agent-photo {
    position: absolute;
    left: 19px;
    top: 13px;
    width: 240px;
    height: 330px;
    background: linear-gradient(180deg, #7a3b36 0%, #2b3f86 45%, #1d2e6a 100%);
    border-radius: 110px 110px 0 0;
  }
  .web {
    position: absolute;
    left: 337px;
    top: 298px;
    font-size: 15px;
    letter-spacing: 4.4px;
    color: var(--white);
  }
</style>
</head>
<body>

<section class="card card--front" aria-label="Business card front">
  <svg class="card__shape" width="600" height="343" viewBox="0 0 600 343" aria-hidden="true">
    <polygon points="352,0 600,0 600,343 352,343 352,99 369,82 352,65" fill="var(--navy)"/>
    <polyline points="346,0 346,63 364,82 346,101 346,343" fill="none" stroke="var(--navy)" stroke-width="2.5"/>
    <rect x="343" y="80" width="8" height="8" fill="var(--maroon)"/>
  </svg>

  <div class="brand"><span class="brand__mark"></span>Corval</div>

  <div class="contact">
    <h1 class="contact__name">DANIEL HART</h1>
    <p class="contact__role">CEO/FOUNDER</p>
    <address class="contact__address">4120 Cedar Hollow Road<br>Juneau<br>Alaska 34512</address>
    <ul class="contact__list">
      <li>
        <svg class="contact__icon" viewBox="0 0 24 24" aria-hidden="true"><path d="M6.6 10.8a15 15 0 0 0 6.6 6.6l2.2-2.2a1 1 0 0 1 1-.25 11.4 11.4 0 0 0 3.6.57 1 1 0 0 1 1 1V20a1 1 0 0 1-1 1A17 17 0 0 1 3 4a1 1 0 0 1 1-1h3.5a1 1 0 0 1 1 1c0 1.25.2 2.45.57 3.57a1 1 0 0 1-.25 1z"/></svg>
        555 204 7719
      </li>
      <li>
        <svg class="contact__icon" viewBox="0 0 24 24" aria-hidden="true"><path d="M7 1h10a2 2 0 0 1 2 2v18a2 2 0 0 1-2 2H7a2 2 0 0 1-2-2V3a2 2 0 0 1 2-2zm0 3v14h10V4zm5 15.5a1 1 0 1 0 0 2 1 1 0 0 0 0-2z"/></svg>
        555 381 6042
      </li>
      <li>
        <svg class="contact__icon" viewBox="0 0 24 24" aria-hidden="true"><path d="M2 5h20v14H2zm2 2v.5l8 5 8-5V7l-8 5z"/></svg>
        dan@corval.com
      </li>
      <li>
        <svg class="contact__icon" viewBox="0 0 24 24" aria-hidden="true"><path d="M12 2a10 10 0 1 0 0 20 10 10 0 0 0 0-20zm-1 17.9A8 8 0 0 1 4.1 11H7c.1 3.3 1.6 6.3 4 8.9zM13 4.1A8 8 0 0 1 19.9 11H17c-.1-2.6-1.5-5.1-4-6.9zm-2 0V11H9c.1-2.6 1-5 2-6.9zm2 15.8V13h2c-.1 2.6-1 5-2 6.9z"/></svg>
        www.corval.com
      </li>
    </ul>
  </div>
</section>

<section class="card card--back" aria-label="Business card back">
  <div class="agent-photo" role="img" aria-label="Portrait photo of the sales executive in a blue suit and striped tie"></div>
  <div class="brand"><span class="brand__mark"></span>Corval</div>
  <div class="web">www.corval.com</div>
</section>

</body>
</html>
```